Business Cards for a law firm

Business cards for our law firm. Use our silhoette logo and OAK PARTNERS - check our website (www.oakpartners.example)

Contact Information for Business Card

our silhouette logo, OAK PARTNERS, 800-555-0147, Dorian Pemberton, dorian@oakpartners.example

Requirements
Must have
• our silhouette logo, OAK PARTNERS, 800-555-0147, Dorian Pemberton, dorian@oakpartners.example

```html
<!DOCTYPE html>
<html lang="en">
<head>
<meta charset="utf-8">
<title>Oak Partners business cards</title>
<link rel="stylesheet" href="https://fonts.googleapis.com/css2?family=Montserrat:wght@600&family=Open+Sans:wght@400;600&display=swap">
<style>
  :root {
    --navy: #1f2f66;
    --paper: #f4f4f3;
    --accent: #f0a22a;
    --backdrop: #cfcfcf;
    --white: #ffffff;
  }
  * { margin: 0; padding: 0; box-sizing: border-box; }
  html, body { width: 1200px; height: 853px; overflow: hidden; }
  body {
    background: var(--backdrop);
    font-family: "Open Sans", Arial, sans-serif;
    display: flex;
    flex-direction: column;
    align-items: center;
    justify-content: center;
    gap: 30px;
  }
  .card {
    position: relative;
    width: 680px;
    height: 389px;
    border-radius: 26px;
    background: var(--paper);
    overflow: hidden;
    box-shadow: 0 6px 18px rgba(0,0,0,0.18);
  }
  /* front */
  .front-panel {
    position: absolute;
    inset: 0 270px 0 0;
    background: var(--navy);
  }
  .figures {
    position: absolute;
    top: 0; right: 0; bottom: 0;
    width: 300px;
    background: linear-gradient(100deg, var(--navy) 0%, var(--navy) 45%, #8d97b8 75%, var(--paper) 100%);
  }
  .brand {
    position: absolute;
    display: flex;
    align-items: center;
    gap: 12px;
    font-family: "Montserrat", Arial, sans-serif;
    font-weight: 600;
    letter-spacing: 2px;
  }
  .brand-dot { border-radius: 50%; flex: none; }
  .front-brand { top: 34px; left: 36px; color: var(--white); font-size: 26px; }
  .front-brand .brand-dot { width: 30px; height: 30px; background: var(--white); }
  .details {
    position: absolute;
    left: 36px;
    top: 132px;
    color: var(--white);
  }
  .firm-name {
    font-family: "Montserrat", Arial, sans-serif;
    font-weight: 600;
    font-size: 20px;
    letter-spacing: 1px;
  }
  .firm-tag { font-size: 9px; letter-spacing: 4.5px; margin-top: 2px; }
  .rule { width: 24px; height: 2px; background: var(--accent); margin: 12px 0 10px; }
  .person-name { font-size: 21px; font-weight: 600; letter-spacing: 1px; }
  .person-role { font-size: 11px; letter-spacing: 1.5px; margin-bottom: 14px; }
  .contact { display: flex; align-items: center; gap: 8px; font-size: 12px; letter-spacing: 0.8px; margin-top: 5px; }
  .contact svg { width: 14px; height: 14px; flex: none; }
  .contact-web { padding-left: 22px; }
  /* back */
  .back-brand {
    top: 50%; left: 50%;
    transform: translate(-50%, -50%);
    color: var(--navy);
    font-size: 36px;
    white-space: nowrap;
  }
  .back-brand .brand-dot { width: 38px; height: 38px; background: var(--navy); }
</style>
</head>
<body>
  <section class="card card-front">
    <div class="front-panel"></div>
    <div class="figures" role="img" aria-label="Two standing figures drawn as navy silhouettes on white"></div>
    <div class="brand front-brand"><span class="brand-dot"></span>OAK PARTNERS</div>
    <div class="details">
      <p class="firm-name">OAK PARTNERS</p>
      <p class="firm-tag">INJURY ATTORNEYS</p>
      <div class="rule"></div>
      <p class="person-name">Dorian Pemberton</p>
      <p class="person-role">ATTORNEY</p>
      <p class="contact contact-phone">
        <svg viewBox="0 0 16 16" aria-hidden="true"><path fill="var(--accent)" d="M3.6 1.5l2.3 2.6-1.3 1.8c.9 2 2.5 3.6 4.5 4.5l1.8-1.3 2.6 2.3-1.4 2.4C6.8 13.5 2.5 9.2 1.2 2.9z"/></svg>
        800-555-0147
      </p>
      <p class="contact contact-email">
        <svg viewBox="0 0 16 16" aria-hidden="true"><rect x="1" y="3" width="14" height="10" fill="var(--accent)"/><path d="M1 3l7 6 7-6" fill="none" stroke="var(--navy)" stroke-width="1.4"/></svg>
        dorian@oakpartners.example
      </p>
      <p class="contact contact-web">www.oakpartners.example</p>
    </div>
  </section>
  <section class="card card-back">
    <div class="brand back-brand"><span class="brand-dot"></span>OAK PARTNERS</div>
  </section>
</body>
</html>
```